Stylish Business Cards Wanted

- DOUBLE SIDED Design Required -

High end, edgy cards for a corporate and personal stylist. Must include logo,
Name: Belinda Harwick
Title: Director and Stylist
telephone : +61 8 7142 5809
email: belinda@theloombriefing.example
website: theloombriefing.example
Tag: Corporate Workwear & Uniform Specialist | Personal Stylist
Would like nice icons for telephone, email, website

Target Market(s)

Businesses wanting stylish uniforms, people wanting stylish wardrobes

Industry/Entity Type

Corporate Workwear Stylist

Contact Information for Business Card

I would like black, white and gold foiling incorporated in the design - possibly a touch of the other colours on my branding guide attached Name: Belinda Harwick Title: Director and Stylist telephone : +61 8 7142 5809 email: belinda@theloombriefing.example website: theloombriefing.example Tag: Corporate Workwear & Uniform Specialist | Personal Stylist Would like nice icons for telephone, email, website

Font styles to use
Other font styles liked:
• Raleway

Colors

Designer to choose colors to be used in the design.

Requirements
Must have
• Gold foil accents

```html
<!DOCTYPE html>
<html lang="en">
<head>
<meta charset="utf-8">
<title>The Loom Briefing — Business Cards</title>
<link rel="stylesheet" href="https://fonts.googleapis.com/css2?family=Raleway:wght@400;500;600&display=swap">
<style>
  :root {
    --backdrop: #ececec;
    --gold-light: #ead25f;
    --gold-mid: #dfbf45;
    --gold-deep: #c9a739;
    --gold-text: #e2b94f;
    --ink: #1c1b1b;
    --paper: #ffffff;
    --paper-shade: #ececec;
    --rule: #3a3a3a;
  }
  * { margin: 0; padding: 0; box-sizing: border-box; }
  html, body { width: 1200px; height: 507px; overflow: hidden; }
  body {
    position: relative;
    background: var(--backdrop);
    font-family: "Raleway", sans-serif;
    color: var(--ink);
  }
  .card {
    position: absolute;
    top: 106px;
    width: 493px;
    height: 296px;
  }
  .card--front {
    left: 83px;
    background: radial-gradient(ellipse at 50% 45%, var(--gold-light) 0%, var(--gold-mid) 50%, var(--gold-deep) 100%);
  }
  .card--back {
    left: 623px;
    background: radial-gradient(ellipse at 55% 50%, var(--paper) 0%, #f7f7f7 50%, var(--paper-shade) 100%);
  }
  .brand-name {
    position: absolute;
    font-weight: 600;
    color: var(--ink);
    text-align: center;
    line-height: 1.05;
    letter-spacing: 0.5px;
  }
  .card--front .brand-name {
    left: 0; right: 0;
    top: 108px;
    font-size: 30px;
  }
  .tagline {
    position: absolute;
    left: 0; right: 0;
    top: 210px;
    text-align: center;
    font-size: 14px;
    font-weight: 400;
  }
  .tagline .sep { margin: 0 4px; }
  .card--back .brand-name {
    left: 40px;
    width: 150px;
    top: 122px;
    font-size: 22px;
  }
  .divider {
    position: absolute;
    left: 198px;
    top: 93px;
    width: 1px;
    height: 109px;
    background: var(--rule);
  }
  .contact {
    position: absolute;
    left: 211px;
    top: 96px;
  }
  .contact__name {
    font-size: 22px;
    font-weight: 600;
    color: var(--gold-text);
    line-height: 1.1;
  }
  .contact__title {
    font-size: 11.5px;
    margin-top: 2px;
  }
  .contact__list { list-style: none; margin-top: 8px; }
  .contact__item {
    display: flex;
    align-items: center;
    height: 21.5px;
    font-size: 14px;
  }
  .contact__icon {
    width: 11px; height: 11px;
    margin-right: 5px;
    flex: none;
  }
</style>
</head>
<body>
  <section class="card card--front" aria-label="Card front">
    <div class="brand-name">The Loom<br>Briefing</div>
    <p class="tagline">Corporate Workwear<span class="sep">|</span>Uniform Specialist<span class="sep">|</span>Personal Stylist</p>
  </section>

  <section class="card card--back" aria-label="Card back">
    <div class="brand-name">The Loom<br>Briefing</div>
    <div class="divider"></div>
    <div class="contact">
      <h1 class="contact__name">Belinda Harwick</h1>
      <p class="contact__title">Director and Stylist</p>
      <ul class="contact__list">
        <li class="contact__item">
          <svg class="contact__icon" viewBox="0 0 12 12" aria-hidden="true">
            <circle cx="6" cy="6" r="6" fill="#e2b94f"/>
            <path d="M3 4.2c0-.6 1.3-1.2 3-1.2s3 .6 3 1.2v.6H7.6v-.6H4.4v.6H3zM4 5.5h4l1 3H3z" fill="#fff"/>
          </svg>
          +61 8 7142 5809
        </li>
        <li class="contact__item">
          <svg class="contact__icon" viewBox="0 0 12 12" aria-hidden="true">
            <circle cx="6" cy="6" r="6" fill="#e2b94f"/>
            <rect x="3" y="4" width="6" height="4.2" fill="#fff"/>
            <path d="M3 4l3 2.3L9 4" fill="none" stroke="#e2b94f" stroke-width=".7"/>
          </svg>
          belinda@theloombriefing.example
        </li>
        <li class="contact__item">
          <svg class="contact__icon" viewBox="0 0 12 12" aria-hidden="true">
            <circle cx="6" cy="6" r="6" fill="#e2b94f"/>
            <g fill="none" stroke="#fff" stroke-width=".7">
              <circle cx="6" cy="6" r="3.2"/>
              <ellipse cx="6" cy="6" rx="1.4" ry="3.2"/>
              <path d="M2.8 6h6.4M3.4 4.5h5.2M3.4 7.5h5.2"/>
            </g>
          </svg>
          theloombriefing.example
        </li>
      </ul>
    </div>
  </section>
</body>
</html>
```